Home Remodeling company needs a business card design

we need a business card design for home remodeling company in hamilton county, indiana USA. we offers a wide range of construction services including whole house renovations, Design and Build Basements and Kitchen and Bathroom Remodeling . we would like to see designs for both site of business card that use the same color of the company logo and also including all information below :
1- Karim Feltous CEO / General Contractor
2- all company contacts Telephone numbers ( 1-888-DULOM-47 ) ( 317-555-0193) email address ( info@dulomhome.com) website ( www.dulomhome.com ) and social media logos (Facebook- twitter- google plus )
3- company logo
4- licensed . insured . bonded

```html
<!DOCTYPE html>
<html lang="en">
<head>
<meta charset="utf-8">
<title>Dulom Home Remodeling – Business Card</title>
<link rel="stylesheet" href="https://fonts.googleapis.com/css2?family=Open+Sans:wght@400;600&display=swap">
<style>
  :root {
    --backdrop: #2a2a2a;
    --card: #141414;
    --brand-red: #d7333f;
    --text-light: #f2f2f2;
  }
  html, body {
    margin: 0;
    padding: 0;
    width: 1200px;
    height: 900px;
    overflow: hidden;
    background: var(--backdrop);
    font-family: "Open Sans", Arial, sans-serif;
  }
  .canvas {
    position: relative;
    width: 1200px;
    height: 900px;
  }
  .card {
    position: absolute;
    top: 307px;
    width: 500px;
    height: 286px;
    border-radius: 16px;
    background: var(--card);
    box-shadow: 0 10px 30px rgba(0,0,0,0.45);
    overflow: hidden;
  }
  .card--front { left: 70px; }
  .card--back { left: 630px; }

  .brand {
    position: absolute;
    margin: 0;
    display: flex;
    align-items: center;
    gap: 10px;
    font-weight: 600;
    font-size: 34px;
    line-height: 1;
    color: var(--text-light);
  }
  .brand__mark {
    width: 9px;
    height: 9px;
    background: var(--brand-red);
  }
  .card--front .brand { left: 36px; top: 112px; }
  .card--back .brand { left: 150px; top: 106px; }

  .contact {
    position: absolute;
    left: 300px;
    top: 76px;
    color: var(--text-light);
  }
  .contact__name {
    margin: 0;
    font-weight: 600;
    font-size: 15px;
    color: var(--brand-red);
  }
  .contact__title {
    margin: 2px 0 22px;
    font-size: 11.5px;
  }
  .contact__list {
    list-style: none;
    margin: 0;
    padding: 0;
  }
  .contact__item {
    display: flex;
    align-items: center;
    gap: 8px;
    font-size: 12.5px;
    line-height: 20px;
  }
  .contact__icon {
    width: 10px;
    height: 10px;
    fill: var(--brand-red);
    flex: none;
  }
  .social {
    display: flex;
    gap: 8px;
    margin: 14px 0 0 18px;
  }
  .social__dot {
    width: 14px;
    height: 14px;
    border-radius: 50%;
    background: var(--text-light);
  }

  .credentials {
    position: absolute;
    left: 150px;
    top: 160px;
    display: flex;
    align-items: center;
    gap: 7px;
    font-weight: 600;
    font-size: 13px;
    color: var(--text-light);
  }
  .credentials__dot {
    width: 6px;
    height: 6px;
    border-radius: 50%;
    background: var(--brand-red);
  }
</style>
</head>
<body>
<main class="canvas">

  <section class="card card--front" aria-label="Card front">
    <p class="brand"><span class="brand__mark"></span><span>DULOM</span></p>

    <div class="contact">
      <p class="contact__name">Karim Feltous</p>
      <p class="contact__title">CEO / General Contractor</p>
      <ul class="contact__list">
        <li class="contact__item">
          <svg class="contact__icon" viewBox="0 0 10 10" aria-hidden="true"><path d="M2 0.5 L3.6 2.6 L2.8 3.6 Q4 6 6.4 7.2 L7.4 6.4 L9.5 8 L8.4 9.5 Q3.5 9 0.5 1.6 Z"/></svg>
          <span>1-888-DULOM-47</span>
        </li>
        <li class="contact__item">
          <svg class="contact__icon" viewBox="0 0 10 10" aria-hidden="true"><path d="M2 0.5 L3.6 2.6 L2.8 3.6 Q4 6 6.4 7.2 L7.4 6.4 L9.5 8 L8.4 9.5 Q3.5 9 0.5 1.6 Z"/></svg>
          <span>317-555-0193</span>
        </li>
        <li class="contact__item">
          <svg class="contact__icon" viewBox="0 0 10 10" aria-hidden="true"><path d="M0 2 H10 V8.5 H0 Z M0 2 L5 5.5 L10 2" stroke="#141414" stroke-width="0.8"/></svg>
          <span>info@dulomhome.com</span>
        </li>
        <li class="contact__item">
          <svg class="contact__icon" viewBox="0 0 10 10" aria-hidden="true"><path d="M6 1 L9 4 L7.5 5.5 L6.8 4.8 L7.6 4 L6 2.4 L4 4.4 L4.6 5 L3.9 5.7 L2.6 4.4 Z M4 9 L1 6 L2.5 4.5 L3.2 5.2 L2.4 6 L4 7.6 L6 5.6 L5.4 5 L6.1 4.3 L7.4 5.6 Z"/></svg>
          <span>www.dulomhome.com</span>
        </li>
      </ul>
      <div class="social">
        <span class="social__dot" role="img" aria-label="Social profile icon"></span>
        <span class="social__dot" role="img" aria-label="Social profile icon"></span>
        <span class="social__dot" role="img" aria-label="Social profile icon"></span>
      </div>
    </div>
  </section>

  <section class="card card--back" aria-label="Card back">
    <p class="brand"><span class="brand__mark"></span><span>DULOM</span></p>
    <div class="credentials">
      <span>Licensed</span><span class="credentials__dot"></span>
      <span>Insured</span><span class="credentials__dot"></span>
      <span>Bonded</span>
    </div>
  </section>

</main>
</body>
</html>
```